Educational Management System User Interface (Vantrel Design Concepts)

Hi,I require a 1-page design for an educational management system. The image attached shows all required elements and also their locations. I require the design to be based on vantrel-styled interfaces using elements from: http://prelk.hostvane.io/prelk-kitframe/ & http://kitframenil.com/kitframe-layout/admin . Side menu's should not be too large that they hide the main content of the page.
Sorry very slight addition to the design as per new uploaded file.
I like how the elements of the vantrel loop page are seperated with the background colour and white boxes. This could maybe work in the design as per the uploaded image?
Thanks,
Gideon

```html
<!DOCTYPE html>
<html lang="en">
<head>
<meta charset="utf-8">
<title>Quorvi – Teacher Dashboard</title>
<link rel="stylesheet" href="https://fonts.googleapis.com/css2?family=Open+Sans:wght@400;600;700&display=swap">
<style>
:root{
  --bar:#636a78;
  --bar-active:#4f5562;
  --bar-line:#575e6b;
  --side:#37acdc;
  --side-row:#4bbde8;
  --side-line:#3aa8d6;
  --side-title:#1e7fa9;
  --green:#8bc34a;
  --panel:#e4e8ee;
  --panel-line:#d2d7de;
  --card:#f4f6f9;
  --text:#5b616b;
  --muted:#9aa0a8;
  --accent:#2fa3dc;
  --alert:#f26a4b;
  --ink:#3e4450;
}
*{box-sizing:border-box;margin:0;padding:0}
html,body{width:1024px;height:1200px;overflow:hidden}
body{font-family:"Open Sans",sans-serif;color:var(--text);background:#fff;position:relative}

.topbar{position:absolute;left:0;top:0;width:1024px;height:59px;background:var(--bar)}
.brand{position:absolute;left:0;top:0;width:179px;height:59px;display:flex;align-items:center;padding-left:23px;
  color:#ffffff;font-weight:400;font-size:19px;border-right:1px solid var(--bar-line)}
.nav{position:absolute;left:179px;top:0;display:flex;height:59px}
.nav a{width:61px;height:59px;display:flex;align-items:center;justify-content:center;border-right:1px solid var(--bar-line)}
.nav a.active{background:var(--bar-active)}
.nav svg{width:18px;height:18px;fill:#c5cad2}
.notify{position:absolute;top:19px}
.notify svg{width:20px;height:20px;fill:#8a909b}
.badge{position:absolute;left:-5px;top:-6px;width:13px;height:13px;border-radius:50%;background:var(--alert);
  color:#fff;font-size:8px;line-height:13px;text-align:center}
.user{position:absolute;left:889px;top:17px;display:flex;align-items:center;gap:9px;color:#fff;font-size:11.2px}
.user .photo{width:24px;height:24px;background:linear-gradient(#e9e9e9,#9a9a9a)}
.user .caret{font-size:8px;color:#aab0ba;margin-left:-4px}

.sidebar{position:absolute;left:0;top:59px;width:179px;height:1141px;background:var(--side)}
.role{position:absolute;left:18px;top:39px;font-size:24px;color:var(--side-title)}
.side-head{position:absolute;left:18px;display:flex;align-items:center;gap:9px;color:#fff;font-weight:700;font-size:12.8px;letter-spacing:.5px}
.side-head svg{width:20px;height:20px;fill:none;stroke:#a9dcf2;stroke-width:1.3}
.side-list{position:absolute;left:0;width:179px}
.side-list li{list-style:none;height:32.5px;line-height:32px;padding-left:22px;background:var(--side-row);
  color:#fff;font-size:11.2px;border-bottom:1px solid var(--side-line)}
.btn-side{position:absolute;left:19px;width:112px;height:27px;background:var(--green);color:#fff;
  font-size:9.5px;text-align:center;line-height:27px;border-radius:1px}

.main{position:absolute;left:179px;top:59px;width:613px;height:1141px;background:#fff}
.refine{position:absolute;left:425px;top:27px;width:160px;height:29px;border:1px solid #e1e4e8;background:#fafbfc;
  font-size:11.2px;color:var(--ink);padding:0 10px;display:flex;align-items:center;justify-content:space-between}
.refine i{border-left:3px solid transparent;border-right:3px solid transparent;border-top:3px solid #333}
.me{position:absolute;left:39px;top:64px;width:51px;height:51px;background:linear-gradient(#6b5848,#caa07c 60%,#3b2e28)}
.composer{position:absolute;left:105px;top:65px;width:480px;height:28px;border:1px solid #e1e4e8;
  font-size:11.2px;color:#9ba1a9;padding:0 11px;line-height:26px}
.tools{position:absolute;left:386px;top:105px;display:flex;gap:14px}
.tools svg{width:13px;height:13px;fill:none;stroke:#6d737d;stroke-width:1.4}
.post-btn{position:absolute;left:471px;top:99px;width:112px;height:27px;background:var(--green);color:#fff;
  font-size:11.2px;text-align:center;line-height:27px;border-radius:1px}
.refresh{position:absolute;left:52px;top:146px;width:18px;height:18px}
.timeline{position:absolute;left:61px;top:165px;width:1px;height:672px;background:#c9ced5}

.avatar{position:absolute;width:51px;height:51px;background:linear-gradient(160deg,#c99b63,#f2d3b3 50%,#b88656)}
.post{position:absolute;background:var(--card);box-shadow:0 1px 2px rgba(0,0,0,.18);padding:22px 18px 0 16px}
.post::before{content:"";position:absolute;left:-9px;top:var(--arrow,50px);border-top:9px solid transparent;
  border-bottom:9px solid transparent;border-right:9px solid var(--card)}
.post header{display:flex;justify-content:space-between;align-items:baseline;font-size:11.2px;color:var(--ink);margin-bottom:10px}
.post time{color:var(--muted);font-size:10.6px}
.post p{font-size:11.2px;line-height:16px}
.post .reply{position:absolute;right:10px;bottom:13px;width:12px;height:12px;fill:var(--accent)}
.attach{position:absolute;left:18px;top:24px;width:60px;text-align:center}
.attach span{display:block;font-size:8.5px;font-weight:600;color:var(--accent);margin-top:4px}

.panel{position:absolute;left:792px;top:59px;width:232px;height:1141px;background:var(--panel)}
.ev-head{position:absolute;left:14px;display:flex;align-items:center;gap:15px;color:#545a66;font-weight:600;font-size:12.8px;letter-spacing:.3px}
.ev-list{position:absolute;left:0;width:232px}
.ev-list li{list-style:none;height:32.8px;border-bottom:1px solid var(--panel-line);display:flex;align-items:center;
  padding:0 9px 0 14px;font-size:11.2px;color:#4b515c}
.ev-list .sep{color:#a3a9b1;margin:0 8px}
.ev-list .dot{margin-left:auto;width:9px;height:9px;border-radius:50%;background:var(--alert);position:relative}
.ev-list .dot::after{content:"";position:absolute;left:4px;top:2px;width:1px;height:5px;background:#fff}
</style>
</head>
<body>

<header class="topbar">
  <div class="brand">Quorvi</div>
  <nav class="nav">
    <a><svg viewBox="0 0 20 20"><path d="M10 2 1 10h3v8h5v-5h2v5h5v-8h3z"/></svg></a>
    <a class="active"><svg viewBox="0 0 20 20"><path d="M2 3h16v14H2zM3.5 7h4v3h-4zm5 0h3v3h-3zm4 0h4v3h-4zm-9 4h4v4.5h-4zm5 0h3v4.5h-3zm4 0h4v4.5h-4z" fill-rule="evenodd"/></svg></a>
    <a><svg viewBox="0 0 20 20"><path d="M2 10.5 4.5 8l3.5 3.5L15.5 4 18 6.5l-10 10z"/></svg></a>
    <a><svg viewBox="0 0 20 20"><path d="M1 4h6l2 2h8v3H5L2 16H1zM5.5 10H19l-3 7H2.5z"/></svg></a>
  </nav>
  <div class="notify" style="left:808px"><svg viewBox="0 0 20 20"><path d="M10 1 19 18H1z"/></svg><span class="badge">6</span></div>
  <div class="notify" style="left:849px"><svg viewBox="0 0 20 20"><path d="M1 8l9 5 9-5v10H1zM1 6h18l-9 5z"/></svg><span class="badge">5</span></div>
  <div class="user"><div class="photo" role="img" aria-label="Profile photo of John Doe"></div>John Doe <span class="caret">&#8964;</span></div>
</header>

<aside class="sidebar">
  <div class="role">Teacher</div>
  <div class="side-head" style="top:83px"><svg viewBox="0 0 20 20"><circle cx="10" cy="6" r="2.5"/><circle cx="4.5" cy="7" r="2"/><circle cx="15.5" cy="7" r="2"/><path d="M6 17v-4a4 4 0 0 1 8 0v4M1 15v-3a3 3 0 0 1 4-2.5M19 15v-3a3 3 0 0 0-4-2.5"/></svg>MY GROUPS</div>
  <ul class="side-list" style="top:115px">
    <li>Group Name</li><li>Group Name</li><li>Group Name</li><li>Group Name</li>
  </ul>
  <div class="btn-side" style="top:261px">Create New Group</div>
  <div class="btn-side" style="top:293px">Join More Group</div>
  <div class="side-head" style="top:350px"><svg viewBox="0 0 20 20"><circle cx="10" cy="10" r="7.5"/><circle cx="10" cy="10" r="3"/><path d="M10 2.5v4.5M10 13v4.5M2.5 10H7M13 10h4.5"/></svg>COMMUNITY</div>
  <ul class="side-list" style="top:382px"><li>Study Owl</li></ul>
</aside>

<main class="main">
  <div class="refine">Refine by Group <i></i></div>
  <div class="me" role="img" aria-label="Photo of the current teacher"></div>
  <div class="composer">Post New Update...</div>
  <div class="tools">
    <svg viewBox="0 0 14 14"><circle cx="4" cy="4" r="2.5"/><circle cx="10" cy="10" r="2.5"/><path d="M5.5 5.5l3 3"/></svg>
    <svg viewBox="0 0 14 14"><path d="M3 1h5l3 3v9H3zM8 1v3h3"/></svg>
    <svg viewBox="0 0 14 14"><path d="M1 4h3l1-2h4l1 2h3v8H1z" fill="#6d737d"/><circle cx="7" cy="8" r="2" stroke="#fff"/></svg>
  </div>
  <div class="post-btn">Post</div>
  <svg class="refresh" viewBox="0 0 20 20" fill="none" stroke="#2fa3dc" stroke-width="2.4"><path d="M16 8A6.5 6.5 0 0 0 4 7M4 12a6.5 6.5 0 0 0 12 1"/><path d="M3 3v4.5h4.5M17 17v-4.5h-4.5" stroke-width="2"/></svg>
  <div class="timeline"></div>

  <div class="avatar" style="left:35px;top:194px" role="img" aria-label="Photo of Anna Molly"></div>
  <article class="post" style="left:105px;top:164px;width:480px;height:130px">
    <header><span>Anna Molly</span><time>12 Dec, 2014 at 12:10</time></header>
    <p>Cras sit amet nibh libero, in gravida nulla. Nulla vel metus scelerisque ante sollicitudin commodo. Cras purus odio, vestibulum in vulputate at, tempus viverra turpis.</p>
    <svg class="reply" viewBox="0 0 12 12"><path d="M5 1 0 5l5 4V6.5c3 0 5 1 6.5 4C11 6 8.5 3.8 5 3.5z"/></svg>
  </article>

  <div class="avatar" style="left:109px;top:339px" role="img" aria-label="Photo of Anna Molly"></div>
  <article class="post" style="left:177px;top:302px;width:408px;height:131px;--arrow:57px;padding-left:19px;padding-top:26px">
    <header><span>Anna Molly</span><time>12 Dec, 2014 at 12:10</time></header>
    <p>Cras sit amet nibh libero, in gravida nulla. Nulla vel metus scelerisque ante sollicitudin commodo. Cras purus odio, vestibulum in vulputate at, tempus viverra turpis.</p>
    <svg class="reply" viewBox="0 0 12 12"><path d="M5 1 0 5l5 4V6.5c3 0 5 1 6.5 4C11 6 8.5 3.8 5 3.5z"/></svg>
  </article>

  <div class="avatar" style="left:35px;top:497px" role="img" aria-label="Photo of Anna Molly"></div>
  <article class="post" style="left:105px;top:467px;width:480px;height:130px;padding-left:88px">
    <div class="attach">
      <svg width="44" height="52" viewBox="0 0 44 52" fill="none" stroke="#4b5260" stroke-width="2"><path d="M2 2h28l12 12v36H2zM30 2v12h12"/><path d="M20 22a10 10 0 1 0 10 10H20z"/><path d="M23 19a10 10 0 0 1 10 10H23z"/></svg>
      <span>results.pdf</span>
    </div>
    <header><span>Anna Molly</span><time>12 Dec, 2014 at 12:10</time></header>
    <p>Cras sit amet nibh libero, in gravida nulla. Nulla vel metus scelerisque ante sollicitudin commodo. Cras purus odio, vestibulum in vulputate at, tempus viverra turpis.</p>
    <svg class="reply" viewBox="0 0 12 12"><path d="M5 1 0 5l5 4V6.5c3 0 5 1 6.5 4C11 6 8.5 3.8 5 3.5z"/></svg>
  </article>

  <div class="avatar" style="left:35px;top:673px" role="img" aria-label="Photo of Anna Molly"></div>
  <article class="post" style="left:105px;top:643px;width:480px;height:130px">
    <header><span>Anna Molly</span><time>12 Dec, 2014 at 12:10</time></header>
    <p>Cras sit amet nibh libero, in gravida nulla. Nulla vel metus scelerisque ante sollicitudin commodo. Cras purus odio, vestibulum in vulputate at, tempus viverra turpis.</p>
    <svg class="reply" viewBox="0 0 12 12"><path d="M5 1 0 5l5 4V6.5c3 0 5 1 6.5 4C11 6 8.5 3.8 5 3.5z"/></svg>
  </article>

  <div class="avatar" style="left:35px;top:839px" role="img" aria-label="Photo of Anna Molly"></div>
  <article class="post" style="left:105px;top:809px;width:480px;height:130px">
    <header><span>Anna Molly</span><time>12 Dec, 2014 at 12:10</time></header>
    <p>Cras sit amet nibh libero, in gravida nulla. Nulla vel metus scelerisque ante sollicitudin commodo. Cras purus odio, vestibulum in vulputate at, tempus viverra turpis.</p>
    <svg class="reply" viewBox="0 0 12 12"><path d="M5 1 0 5l5 4V6.5c3 0 5 1 6.5 4C11 6 8.5 3.8 5 3.5z"/></svg>
  </article>

  <div class="avatar" style="left:109px;top:985px" role="img" aria-label="Photo of Anna Molly"></div>
  <article class="post" style="left:177px;top:947px;width:408px;height:131px;--arrow:57px;padding-left:19px;padding-top:26px">
    <header><span>Anna Molly</span><time>12 Dec, 2014 at 12:10</time></header>
    <p>Cras sit amet nibh libero, in gravida nulla. Nulla vel metus scelerisque ante sollicitudin commodo. Cras purus odio, vestibulum in vulputate at, tempus viverra turpis.</p>
    <svg class="reply" viewBox="0 0 12 12"><path d="M5 1 0 5l5 4V6.5c3 0 5 1 6.5 4C11 6 8.5 3.8 5 3.5z"/></svg>
  </article>
</main>

<aside class="panel">
  <div class="ev-head" style="top:24px">
    <svg width="40" height="40" viewBox="0 0 40 40" fill="none" stroke="#4b5260" stroke-width="1.8"><rect x="1" y="5" width="38" height="34" rx="3"/><path d="M1 12h38M9 1v8M15 1v8M21 1v8M27 1v8M33 1v8"/><text x="20" y="34" text-anchor="middle" font-family="Open Sans, sans-serif" font-size="20" fill="#4b5260" stroke="none">25</text></svg>
    TODAY'S EVENTS
  </div>
  <ul class="ev-list" style="top:74px">
    <li>12:15<span class="sep">|</span>Meeting in Canteen<span class="dot"></span></li>
    <li>12:15<span class="sep">|</span>Meeting in Canteen<span class="dot"></span></li>
    <li>12:15<span class="sep">|</span>Meeting in Canteen<span class="dot"></span></li>
    <li>12:15<span class="sep">|</span>Meeting in Canteen<span class="dot"></span></li>
    <li>12:15<span class="sep">|</span>Meeting in Canteen<span class="dot"></span></li>
  </ul>
  <div class="ev-head" style="top:266px">
    <svg width="40" height="40" viewBox="0 0 40 40" fill="none" stroke="#4b5260" stroke-width="1.8"><rect x="1" y="5" width="38" height="34" rx="3"/><path d="M1 12h38M9 1v8M15 1v8M21 1v8M27 1v8M33 1v8"/><text x="20" y="34" text-anchor="middle" font-family="Open Sans, sans-serif" font-size="20" fill="#4b5260" stroke="none">25</text></svg>
    UPCOMING EVENTS
  </div>
  <ul class="ev-list" style="top:315px">
    <li>12:15<span class="sep">|</span>Meeting in Canteen<span class="dot"></span></li>
    <li>12:15<span class="sep">|</span>Meeting in Canteen<span class="dot"></span></li>
    <li>12:15<span class="sep">|</span>Meeting in Canteen<span class="dot"></span></li>
    <li>12:15<span class="sep">|</span>Meeting in Canteen<span class="dot"></span></li>
    <li>12:15<span class="sep">|</span>Meeting in Canteen<span class="dot"></span></li>
  </ul>
</aside>

</body>
</html>
```